Velk Partners Building Business Cards

We need a business card that reflects our business as "Solar Experts" in San Diego. Browse our website www.velkpartners.example our License needs to be displayed as "CSLB# 3867140" our phone number is (619) 555-0187

Save thousands on your electric bills and increase the value of your home while helping to protect the environment. Our solar installation experts will help you design the system that's right for you, using only the highest quality equipment that will look great and give you ideal performance. Our goal is to make you energy independent, and get your electric bill to 0.

Paul Osterby
(619) 555-0187
paul@velkpartners.example

Target Market(s)

Home owners in san diego looking for solar

Industry/Entity Type

Solar Energy

Contact Information for Business Card

Paul Osterby
(619) 555-0187
paul@velkpartners.example

Font styles to use
Other font styles liked:
• Use our logo font

Requirements
Must have
• License needs to be displayed as "CSLB# 3867140" our phone number is (619) 555-0187
Nice to have
• Real images of rooftop home solar in san diego
Should not have
• our business address

```html
<!DOCTYPE html>
<html lang="en">
<head>
<meta charset="utf-8">
<title>Velk Partners Building – Business Card</title>
<link rel="stylesheet" href="https://fonts.googleapis.com/css2?family=Open+Sans:wght@400;600;700;800&display=swap">
<style>
  :root {
    --navy: #1f3f86;
    --navy-deep: #17336f;
    --sun: #f5ad12;
    --paper: #ffffff;
    --ink-soft: #555a63;
    --stage: #ecebe8;
  }
  * { box-sizing: border-box; margin: 0; padding: 0; }
  html, body { width: 1200px; height: 950px; overflow: hidden; }
  body {
    background: var(--stage);
    font-family: "Open Sans", Arial, sans-serif;
    position: relative;
  }
  .card {
    position: absolute;
    top: 125px;
    width: 400px;
    height: 700px;
    background: var(--paper);
    box-shadow: 0 8px 24px rgba(0,0,0,0.15);
    overflow: hidden;
  }
  .card--front { left: 150px; }
  .card--back { left: 650px; }

  .brand {
    position: absolute;
    top: 70px;
    left: 0;
    width: 100%;
    display: flex;
    justify-content: center;
    align-items: center;
    gap: 10px;
  }
  .brand__dot {
    width: 18px; height: 18px;
    border-radius: 50%;
    background: var(--sun);
  }
  .brand__name {
    color: var(--navy);
    font-weight: 800;
    font-size: 27px;
    letter-spacing: -0.3px;
  }
  .wave-band { position: absolute; left: 0; top: 0; width: 400px; height: 700px; }

  .contact {
    position: absolute;
    left: 92px;
    top: 395px;
    color: var(--paper);
  }
  .contact__name {
    color: var(--sun);
    font-weight: 700;
    font-size: 31px;
    line-height: 1.1;
  }
  .contact__role {
    font-size: 21px;
    margin-top: 4px;
  }
  .contact__license {
    font-size: 16px;
    margin-top: 22px;
    margin-left: 2px;
  }
  .contact__list { list-style: none; margin-top: 10px; }
  .contact__item {
    display: flex;
    align-items: center;
    gap: 8px;
    font-size: 16px;
    line-height: 1.55;
  }
  .contact__icon { width: 14px; height: 14px; flex: none; }

  .back__brand {
    position: absolute;
    top: 300px;
    left: 0;
    width: 100%;
    display: flex;
    justify-content: center;
    align-items: center;
    gap: 12px;
  }
  .back__brand .brand__dot { width: 26px; height: 26px; }
  .back__brand .brand__name { font-size: 30px; }
  .back__web {
    position: absolute;
    bottom: 70px;
    width: 100%;
    text-align: center;
    color: var(--ink-soft);
    font-size: 15px;
    letter-spacing: 4px;
  }
</style>
</head>
<body>
  <section class="card card--front" aria-label="Card front">
    <svg class="wave-band" viewBox="0 0 400 700" aria-hidden="true">
      <path d="M0 265 C 70 230, 130 240, 210 285 C 280 325, 340 320, 400 290 L400 700 L0 700 Z" fill="var(--sun)"/>
      <path d="M0 282 C 70 248, 130 258, 210 303 C 280 343, 340 338, 400 308 L400 700 L0 700 Z" fill="var(--navy)"/>
    </svg>
    <div class="brand">
      <span class="brand__name">Velk Partners Building</span>
      <span class="brand__dot"></span>
    </div>
    <div class="contact">
      <p class="contact__name">Paul Osterby</p>
      <p class="contact__role">CEO/Founder</p>
      <p class="contact__license">CSLB# 3867140</p>
      <ul class="contact__list">
        <li class="contact__item">
          <svg class="contact__icon" viewBox="0 0 16 16" aria-hidden="true"><path d="M3.5 1.5 6 4.5 4.7 6.3c.9 2 2.5 3.6 4.5 4.5L11 9.5l3 2.5-1.5 2.5C7 14.5 1.5 9 1.5 3.5Z" fill="var(--sun)"/></svg>
          <span>(619) 555-0187</span>
        </li>
        <li class="contact__item">
          <svg class="contact__icon" viewBox="0 0 16 16" aria-hidden="true"><rect x="1" y="3" width="14" height="10" rx="1.5" fill="var(--sun)"/><path d="M1.5 4 8 9l6.5-5" fill="none" stroke="var(--navy)" stroke-width="1.3"/></svg>
          <span>paul@velkpartners.example</span>
        </li>
        <li class="contact__item">
          <svg class="contact__icon" viewBox="0 0 16 16" aria-hidden="true"><circle cx="8" cy="8" r="7" fill="var(--sun)"/><path d="M1 8h14M8 1c-3 3.5-3 10.5 0 14M8 1c3 3.5 3 10.5 0 14" fill="none" stroke="var(--navy)" stroke-width="1"/></svg>
          <span>www.velkpartners.example</span>
        </li>
      </ul>
    </div>
  </section>

  <section class="card card--back" aria-label="Card back">
    <div class="back__brand">
      <span class="brand__name">Velk Partners Building</span>
      <span class="brand__dot"></span>
    </div>
    <p class="back__web">www.velkpartners.example</p>
  </section>
</body>
</html>
```